Business Card for my New Brokerage

Looking to get a business card design for my new Real Estate Brokerage.
I want it with Picture, Phone Number, Email, Website, Office Address
Name and Designation. Please add logo too.

Target Market(s)

Real Estate Investors or Home Buyers

Industry/Entity Type

Real Estate

Contact Information for Business Card

Name, Email, Phone Number, website, email, office address

Colors
EB3D1F
EC4F4E
F09395
F8D3D4
FCEDEE

Requirements
Must have
• Minimalistic, Clean, Modern, Photo
Nice to have
• White and Red Colors

```html
<!DOCTYPE html>
<html lang="en">
<head>
<meta charset="utf-8">
<title>Beacon Realty — Business Card</title>
<link href="https://fonts.googleapis.com/css2?family=Montserrat:wght@500;800&family=Arimo:wght@400;700&display=swap" rel="stylesheet">
<style>
  :root {
    --brand-red: #d9070c;
    --ink: #1e1e1e;
    --paper: #f7f7f7;
    --backdrop: #dcdcdc;
    --photo-bg: #d2d2d2;
    --photo-suit: #3a3a3a;
    --rule: #b9b9b9;
  }
  * { margin: 0; padding: 0; box-sizing: border-box; }
  html, body { width: 1200px; height: 930px; overflow: hidden; }
  body {
    background: var(--backdrop);
    font-family: "Arimo", Arial, sans-serif;
    color: var(--ink);
    position: relative;
  }
  .card {
    position: absolute;
    top: 300px;
    width: 540px;
    height: 310px;
    border-radius: 4px;
    box-shadow: 0 10px 26px rgba(0,0,0,.18);
    overflow: hidden;
  }
  .card--front { left: 40px; background: var(--paper); }
  .card--back {
    left: 620px;
    background: var(--brand-red);
    display: flex;
    align-items: center;
    justify-content: center;
  }
  .headshot {
    position: absolute;
    left: 40px; top: 28px;
    width: 190px; height: 130px;
    border-radius: 14px;
    background: linear-gradient(180deg, var(--photo-bg) 0%, var(--photo-bg) 55%, var(--photo-suit) 100%);
  }
  .profile { position: absolute; left: 40px; top: 176px; }
  .profile__name {
    font-family: "Montserrat", sans-serif;
    font-weight: 800;
    font-size: 20px;
    color: var(--brand-red);
    letter-spacing: .3px;
    text-transform: uppercase;
  }
  .profile__title { font-size: 14px; margin-top: 3px; }
  .contact { list-style: none; margin-top: 12px; font-size: 13.5px; }
  .contact li { display: flex; align-items: center; gap: 8px; margin-bottom: 6px; }
  .contact svg { width: 14px; height: 14px; fill: var(--brand-red); flex: none; }
  .brand {
    position: absolute;
    left: 290px; top: 70px;
    display: flex; align-items: center; gap: 10px;
    font-family: "Montserrat", sans-serif;
    font-weight: 800;
    font-size: 30px;
    letter-spacing: .5px;
    color: var(--brand-red);
    text-transform: uppercase;
  }
  .brand__dot { width: 12px; height: 12px; background: currentColor; }
  .card--back .brand { position: static; color: #fff; font-size: 40px; }
  .divider {
    position: absolute;
    left: 262px; top: 200px;
    width: 1px; height: 70px;
    background: var(--rule);
  }
  .office { position: absolute; left: 290px; top: 200px; font-size: 14px; line-height: 1.45; }
  .office__web { margin-top: 14px; }
  .office__web span { color: var(--brand-red); }
</style>
</head>
<body>
  <section class="card card--front">
    <div class="headshot" role="img" aria-label="Portrait photo of the managing director in a dark suit"></div>
    <div class="profile">
      <h1 class="profile__name">Marcus Hale</h1>
      <p class="profile__title">Managing Director</p>
      <ul class="contact">
        <li>
          <svg viewBox="0 0 24 24" aria-hidden="true"><path d="M6.6 10.8a15.1 15.1 0 0 0 6.6 6.6l2.2-2.2a1 1 0 0 1 1-.25 11.4 11.4 0 0 0 3.6.57 1 1 0 0 1 1 1V20a1 1 0 0 1-1 1A17 17 0 0 1 3 4a1 1 0 0 1 1-1h3.5a1 1 0 0 1 1 1c0 1.25.2 2.45.57 3.57a1 1 0 0 1-.25 1z"/></svg>
          044-555 210 387
        </li>
        <li>
          <svg viewBox="0 0 24 24" aria-hidden="true"><path d="M2 5h20v14H2zm2 2v.4l8 5.2 8-5.2V7z"/></svg>
          hello@beaconrealty.com
        </li>
      </ul>
    </div>
    <div class="brand"><span class="brand__dot"></span>Beacon Realty</div>
    <div class="divider"></div>
    <div class="office">
      <p>218, Harbor View Avenue<br>60714, Fairmont City</p>
      <p class="office__web">www.<span>beaconrealty</span>.com</p>
    </div>
  </section>

  <section class="card card--back">
    <div class="brand"><span class="brand__dot"></span>Beacon Realty</div>
  </section>
</body>
</html>
```